Family business needs stationery redesign with new logo

Family owned company, established in 1987 wanting a brand 'refresh'. We are an electrical, refrigeration and construction company based in the Barkly Region Northern Territory, Australia. We have a new logo we would like to use which is uploaded along with our current letterhead and email signature. We are also dropping the word 'contractors' so please do not include this on any designs. Please note also, the 'orange' color used in our logo and designs should be Northern Territory red ochre which is as follows:

RGB (Hex): #C75B12
PantoneĀ® 159 C
CMYK: 1 / 74 / 100 / 7

We are needing our stationery redesigned using our new logo. Please include letterheads, business cards, envelopes, and email signatures.

We currently use our business letterheads for quotations, invoices, letters, HR matters, and internal memos.

We also need a separate simplified letterhead for internal paperwork such as employee leave forms, meeting agendas, and meeting minutes etc.

Reason: Needing more submissions of full package designs. We are wanting all our stationery, including business cards, letterheads, email signatures, envelopes, etc to be cohesive. We also require ALL the information, as supplied on our template letterhead, to be included on the new letterhead designs. including electrical license no.etc Thank you, R&W

Reason: needing more time as work has got in the way of looking over designs. A lot of designs not meeting the brief/criteria.

Industry/Entity Type

Business

Colors
0355a3
f37122

Requirements
Must have
• The 'orange' color used in the designs should be Northern Territory red ochre which is as follows:
• RGB (Hex): #C75B12
• PantoneĀ® 159 C
• CMYK: 1 / 74 / 100 / 7
• ***MUST INCLUDE ALL INFORMATION THAT IS ON OUR CURRENT LETTERHEAD***
Should not have
• Please do not include the word 'contractors'

```html
<!DOCTYPE html>
<html lang="en">
<head>
<meta charset="utf-8">
<title>R&amp;W Stationery</title>
<link rel="stylesheet" href="https://fonts.googleapis.com/css2?family=Source+Sans+3:wght@400;600;800&display=swap">
<style>
:root{
  --navy:#1b2f6e;
  --ochre:#c75b12;
  --paper:#ffffff;
  --page:#e4e4e4;
  --ink:#2b2b2b;
}
*{margin:0;padding:0;box-sizing:border-box}
html,body{width:1200px;height:715px;overflow:hidden;background:var(--page);font-family:"Source Sans 3",sans-serif;color:var(--ink)}
.canvas{position:relative;width:1200px;height:715px}
.sheet{position:absolute;background:var(--paper);box-shadow:0 2px 6px rgba(0,0,0,.25)}
.wordmark{font-weight:800;color:var(--navy);letter-spacing:1px;line-height:1;display:flex;align-items:center;gap:8px}
.wordmark .dot{display:inline-block;border-radius:50%;background:var(--ochre)}
.wordmark.light{color:#fff}

/* letterhead */
.letterhead{left:188px;top:66px;width:440px;height:620px}
.letterhead .wordmark{position:absolute;left:0;right:0;top:46px;justify-content:center;font-size:38px}
.letterhead .tagline{position:absolute;left:0;right:0;top:98px;text-align:center;font-size:10px;color:var(--navy)}
.letter-body{position:absolute;left:33px;top:224px;width:376px;font-size:7.6px;line-height:9.6px;color:#222}
.letter-body p{margin-bottom:8.5px}
.letter-sign{position:absolute;left:33px;top:405px;font-size:7.6px}
.letter-foot{position:absolute;left:0;bottom:0;width:100%;height:46px;background:var(--navy);border-top:2px solid var(--ochre);color:#fff;text-align:center;font-size:7.6px;line-height:10.8px;padding-top:5px}
.letter-foot b{color:var(--ochre);font-weight:400}

/* business cards */
.card{width:240px;height:138px;border-radius:6px;overflow:hidden}
.card-front{left:48px;top:160px}
.card-front .top{height:80px;display:flex;justify-content:center;align-items:center;border-bottom:2px solid var(--ochre)}
.card-front .top .wordmark{font-size:30px}
.card-info{background:var(--navy);color:#fff;display:flex;justify-content:space-between}
.card-front .card-info{height:58px;padding:8px 12px 0;font-size:6.2px;line-height:9px}
.card-info .name{color:var(--ochre);font-size:8.5px;line-height:9px}
.card-info .contacts{text-align:right}
.card-info .contacts span{display:inline-block;width:5px;height:5px;border-radius:50%;background:var(--ochre);margin-left:4px;vertical-align:middle}
.card-back{background:var(--navy);display:flex;flex-direction:column;align-items:center;justify-content:center}
.card-back .wordmark{font-size:30px;margin-bottom:20px}
.card-back .est{font-size:9.5px;letter-spacing:.5px}
.back-one{left:48px;top:324px}
.back-one .est{color:var(--ochre)}
.back-two{left:48px;top:482px}
.back-two .est{color:#fff}

.card-wide{left:748px;top:44px;width:284px;height:138px}
.card-wide .top{height:72px;display:flex;justify-content:center;align-items:center;border-bottom:3px solid var(--ochre)}
.card-wide .top .wordmark{font-size:32px}
.card-wide .card-info{height:63px;padding:9px 14px 0;font-size:8px;line-height:11.8px}
.card-wide .card-info .name{font-size:11px;line-height:12px}

/* envelopes */
.envelope{width:518px;height:232px;overflow:hidden}
.env-back{left:642px;top:210px}
.env-back svg{position:absolute;left:0;top:0}
.env-back .wordmark{position:absolute;left:0;right:0;top:33px;justify-content:center;font-size:28px}
.env-front{left:642px;top:456px}
.env-front .wordmark{position:absolute;left:34px;top:32px;font-size:34px}
.env-front .return{position:absolute;left:25px;top:183px;font-size:7.8px;line-height:11px;color:#444}
.env-front .band{position:absolute;left:0;bottom:0;width:100%;height:15px;background:var(--navy);border-top:3px solid var(--ochre)}
</style>
</head>
<body>
<div class="canvas">

  <section class="sheet letterhead">
    <div class="wordmark">R&amp;W</div>
    <div class="tagline">Electrical - Refrigeration - Building Services</div>
    <div class="letter-body">
      <p>Lorem ipsum dolor sit amet, consectetur adipiscing elit. Donec orci purus, luctus vitae dignissim eu, iaculis sed purus. Vivamus faucibus, ipsum nec aliquet viverra, leo mauris condimentum ligula, sit amet sagittis enim ligula quis arcu. Nam egestas tortor id nisi porttitor mattis. In tortor ante, ultricies in suscipit a, tempus non massa. Vivamus et auctor mi.</p>
      <p>Nulla facilisi. Integer at lacus vel lacus feugiat porta. Phasellus nec eros mauris, et scelerisque orci. Donec malesuada orci vitae nulla accumsan scelerisque accumsan iaculis magna sit amet fringilla. Maecenas consequat, magna eget tincidunt rutrum mi, id feugiat ante nisi eu risus. Vestibulum nunc orci, rhoncus a placerat in, ultricies varius eros, vel fringilla nisi suscipit eget.</p>
      <p>Aliquam erat volutpat. Curabitur vehicula sagittis nulla at porttitor. Mauris a justo et tellus interdum tristique. Sed id augue vitae urna aliquet a quam. Pellentesque arcu velit, cursus et malesuada ut, consequat et diam. Nullam ullamcorper vitae, rhoncus et arcu. In ultricies ultricies nulla, ut rutrum nisi iaculis at. Donec ornare faucibus.</p>
      <p>Praesent vel lectus ultricies. Morbi semper, est id tincidunt gravida, sem arcu adipiscing lacus, ac bibendum Quisque nec diam sed risus consectetur a ccumsan quis quis nibh. Vestibulum id purus lorem.</p>
    </div>
    <div class="letter-sign">Kate Lowe</div>
    <footer class="letter-foot">
      42 Ridge St, PO Box, Wattle Creek NT. 0862<br>
      ABN 63 208 417 | Refrigerant Trading Authorisation 402318 | NT Electrical Contractors License 51284<br>
      <b>P</b> : 08 8955 0142 &nbsp;<b>F</b> : 08 8955 0176 &nbsp;<b>E</b> : info@rwservices.com.au &nbsp;<b>W</b> : rwservices.com.au
    </footer>
  </section>

  <section class="sheet card card-front">
    <div class="top"><div class="wordmark">R&amp;W</div></div>
    <div class="card-info">
      <div><div class="name">ALAN MARSH</div>CEO/FOUNDER<br>24 Gumtree Way<br>Dalwood, NT 0870</div>
      <div class="contacts">612 555 0148<span></span><br>612 555 0193<span></span><br>alan@rwservices.au<span></span><br>www.rwservices.au<span></span></div>
    </div>
  </section>

  <section class="sheet card card-back back-one">
    <div class="wordmark light">R&amp;W</div>
    <div class="est">Est. 1987</div>
  </section>

  <section class="sheet card card-back back-two">
    <div class="wordmark light">R&amp;W</div>
    <div class="est">Est. 1987</div>
  </section>

  <section class="sheet card-wide" style="position:absolute">
    <div class="top"><div class="wordmark">R&amp;W</div></div>
    <div class="card-info">
      <div><div class="name">ALAN MARSH</div>CEO/FOUNDER<br><span style="display:block;height:4px"></span>24 Gumtree Way<br>Dalwood, NT 0870</div>
      <div class="contacts">612 555 0148<span></span><br>612 555 0193<span></span><br>alan@rwservices.au<span></span><br>www.rwservices.au<span></span></div>
    </div>
  </section>

  <section class="sheet envelope env-back">
    <svg width="518" height="232" viewBox="0 0 518 232">
      <path d="M0 232 L200 86 M518 232 L318 86" stroke="#dcdcdc" stroke-width="1.5" fill="none"/>
      <path d="M0 0 H518 L508 70 Q504 86 486 86 H32 Q14 86 10 70 Z" fill="var(--ochre)"/>
    </svg>
    <div class="wordmark">R&amp;W</div>
  </section>

  <section class="sheet envelope env-front">
    <div class="wordmark">R&amp;W</div>
    <div class="return">42 Ridge St, PO Box<br>Wattle Creek NT. 0862</div>
    <div class="band"></div>
  </section>

</div>
</body>
</html>
```